Business Card Design

The Kestrel Lodge Inn is the most centrally located motel in Grafton.
We are the only family owned motel in Grafton.
Our colour scheme is blue, whiteand black.

I have uploaded a photo of our new rooms and the logo for you to use Thanks. Looking good

Industry/Entity Type

Motel

Contact Information for Business Card

The Kestrel Lodge Inn
Gareth & Lorna Pelling
Owner/Operators
14-16 Wexbury Lane, Grafton NSW 2460
Ph: 02 6617 3904
Email: thekestrellodgeinn@mailvista.example
reception@kestrellodgeinn.example.au
www.kestrellodgeinn.example.au

Colors
0392cd
0455a3

```html
<!DOCTYPE html>
<html lang="en">
<head>
<meta charset="utf-8">
<title>The Kestrel Lodge Inn – Business Card</title>
<link rel="stylesheet" href="https://fonts.googleapis.com/css2?family=Tinos&display=swap">
<style>
  :root {
    --page-bg: #e9e9e9;
    --card-white: #ffffff;
    --ink: #111111;
    --wall-light: #efe6b4;
    --wall-mid: #d8c98a;
    --linen: #f4f4f2;
    --carpet: #4a5a4e;
    --card-shadow: rgba(0, 0, 0, 0.18);
  }
  html, body {
    margin: 0;
    padding: 0;
    width: 1200px;
    height: 772px;
    overflow: hidden;
    background: var(--page-bg);
  }
  .card {
    position: absolute;
    left: 50px;
    top: 71px;
    width: 1100px;
    height: 629px;
    background: var(--card-white);
    box-shadow: 0 4px 14px var(--card-shadow);
    overflow: hidden;
    font-family: "Tinos", "Times New Roman", serif;
    color: var(--ink);
  }
  .card-art {
    position: absolute;
    inset: 0;
    width: 1100px;
    height: 629px;
  }
  .brand {
    position: absolute;
    left: 530px;
    width: 540px;
    top: 62px;
    text-align: center;
    white-space: nowrap;
  }
  .brand-name {
    margin: 0;
    font-size: 33px;
    font-weight: 400;
    letter-spacing: 1px;
    line-height: 1;
  }
  .brand-owners {
    margin: 16px 0 0;
    font-size: 27px;
    line-height: 1;
  }
  .brand-role {
    margin: 10px 0 0;
    font-size: 21px;
    line-height: 1;
  }
  .contact-list {
    position: absolute;
    left: 40px;
    top: 478px;
    margin: 0;
    padding: 0;
    list-style: none;
    font-size: 22px;
    white-space: nowrap;
  }
  .contact-item {
    display: flex;
    align-items: center;
    height: 38px;
  }
  .contact-icon {
    width: 24px;
    height: 22px;
    margin-right: 23px;
    fill: var(--ink);
    flex: none;
  }
</style>
</head>
<body>
<div class="card">
  <svg class="card-art" viewBox="0 0 1100 629" xmlns="http://www.w3.org/2000/svg">
    <defs>
      <linearGradient id="roomTones" x1="0" y1="0" x2="1" y2="1">
        <stop offset="0" stop-color="#8a5a3a"/>
        <stop offset="0.25" stop-color="var(--wall-mid)"/>
        <stop offset="0.5" stop-color="var(--wall-light)"/>
        <stop offset="0.7" stop-color="var(--linen)"/>
        <stop offset="1" stop-color="var(--carpet)"/>
      </linearGradient>
    </defs>
    <rect class="room-photo" role="img" aria-label="Photo of a motel guest room with a made double bed, red throw and timber bedhead" x="0" y="0" width="1100" height="629" fill="url(#roomTones)"/>
    <path class="curve-top" fill="var(--card-white)"
      d="M416 0 C470 110 560 190 660 232 C760 272 900 286 1100 285 L1100 0 Z"/>
    <path class="curve-bottom" fill="var(--card-white)"
      d="M0 239 C150 236 300 268 420 352 C520 420 600 520 709 629 L0 629 Z"/>
  </svg>

  <header class="brand">
    <h1 class="brand-name">THE KESTREL LODGE INN</h1>
    <p class="brand-owners">Gareth &amp; Lorna Pelling</p>
    <p class="brand-role">Operators</p>
  </header>

  <ul class="contact-list">
    <li class="contact-item">
      <svg class="contact-icon" viewBox="0 0 24 22" aria-hidden="true">
        <path d="M2 7 C2 3 6 2 12 2 C18 2 22 3 22 7 L22 9 L17 9 L17 6 L7 6 L7 9 L2 9 Z"/>
        <path d="M6 10 L18 10 L21 20 L3 20 Z"/>
      </svg>
      <span class="contact-phone">02 6617 3904</span>
    </li>
    <li class="contact-item">
      <svg class="contact-icon" viewBox="0 0 24 22" aria-hidden="true">
        <path d="M1 3 H23 V19 H1 Z M3 5 V6 L12 12 L21 6 V5 Z"/>
      </svg>
      <span class="contact-email">thekestrellodgeinn@mailvista.example</span>
    </li>
    <li class="contact-item">
      <svg class="contact-icon" viewBox="0 0 24 22" aria-hidden="true">
        <path d="M12 1 C7.5 1 5 4.2 5 8 C5 13 12 21 12 21 C12 21 19 13 19 8 C19 4.2 16.5 1 12 1 Z M12 5.5 A2.6 2.6 0 1 1 12 10.7 A2.6 2.6 0 1 1 12 5.5 Z" fill-rule="evenodd"/>
      </svg>
      <span class="contact-address">14-16 Wexbury Lane, Marrowby NSW 2471</span>
    </li>
  </ul>
</div>
</body>
</html>
```